Jewelers Website

This is for the DESIGN ONLY.
I am a software programmer and will be doing the development.
New website design for
www.lunacrestgems.com.au
Need a fresh new look for an online only jewellery business who produce their jewellery by hand. I would like it designed in a parallax style. Feel free to recommend fonts to use for the site. This is an Australian based company located in NSW so shots of sites in NSW might make nice background images.
http://vornaplex.me/demo/#theme=parallax
To contain the below sections
About Us
Contact Us
Gallery
Testimonials
Diamond Types
The colour scheme is to be Black / White and Silver.
With the Parallax style there will be moving sections and images for added impact.
Target Market(s)
Young Adults mainly engagement jewellery

```html
<!DOCTYPE html>
<html lang="en">
<head>
<meta charset="utf-8">
<title>Lunacrest Gems</title>
<link href="https://fonts.googleapis.com/css2?family=Arimo:wght@400;700&family=Roboto+Condensed:wght@400;500&display=swap" rel="stylesheet">
<style>
  :root {
    --ink: #222222;
    --ink-soft: #2b2b2b;
    --white: #ffffff;
    --silver: #d9dcdf;
    --text-grey: #555a5e;
    --accent: #f2d23c;
    --font: "Arimo", Arial, sans-serif;
    --display: "Roboto Condensed", "Arial Narrow", sans-serif;
  }
  * { margin: 0; padding: 0; box-sizing: border-box; }
  html, body { width: 1200px; height: 3607px; overflow: hidden; }
  body { position: relative; font-family: var(--font); background: var(--white); color: var(--ink); }
  .section { position: absolute; left: 0; width: 1200px; }
  .abs { position: absolute; }
  .heading { position: absolute; left: 0; width: 1200px; text-align: center; font-family: var(--display); font-size: 70px; font-weight: 500; line-height: 1; }

  /* Navigation */
  .site-nav { top: 0; height: 101px; background: var(--ink); }
  .brand { left: 130px; top: 24px; color: var(--white); font-size: 24px; line-height: 27px; letter-spacing: 1px; }
  .nav-link { top: 38px; color: var(--white); font-size: 15px; text-decoration: none; }
  .nav-link.is-active { color: var(--accent); }

  /* Hero */
  .hero { top: 101px; height: 505px; overflow: hidden; }
  .hero-photo { position: absolute; inset: 0;
    background:
      radial-gradient(ellipse 170px 120px at 110px 230px, rgba(255,240,190,.95) 0%, rgba(255,190,110,.7) 40%, rgba(255,160,90,0) 100%),
      radial-gradient(ellipse 700px 160px at 300px 250px, rgba(245,150,90,.75) 0%, rgba(245,150,90,0) 100%),
      radial-gradient(ellipse 260px 200px at 120px 440px, rgba(230,120,70,.75) 0%, rgba(230,120,70,0) 100%),
      linear-gradient(180deg, #5d5868 0%, #8a7482 18%, #c68a86 32%, #e9a476 44%, #c98a74 52%, #8b7a7c 60%, #6d6466 72%, #3a2f2e 86%, #1f1a19 100%); }
  .hero-title { top: 158px; font-family: var(--font); font-size: 62px; font-weight: 700; color: var(--ink); }
  .hero-sub { top: 243px; font-family: var(--font); font-size: 42px; font-weight: 400; color: var(--white); }
  .hero-arrow { top: 197px; width: 75px; height: 68px; background: rgba(80,80,80,.55); }
  .hero-arrow svg { display: block; margin: 16px auto 0; }

  /* About */
  .about { top: 606px; height: 508px; }
  .about-photo { position: absolute; inset: 0;
    background:
      radial-gradient(ellipse 380px 120px at 900px 150px, rgba(170,178,188,.45) 0%, rgba(170,178,188,0) 100%),
      radial-gradient(ellipse 500px 90px at 400px 330px, rgba(190,198,206,.5) 0%, rgba(190,198,206,0) 100%),
      linear-gradient(180deg, #f3f4f5 0%, #e6e9ec 45%, #dadee2 70%, #e4e6e8 100%); }
  .about .heading { top: 57px; }
  .about-text { left: 145px; width: 910px; top: 142px; text-align: center; font-size: 13px; line-height: 27px; color: var(--text-grey); }
  .service { top: 841px; width: 183px; height: 183px; border-radius: 50%; background: var(--ink); color: var(--white);
    display: flex; align-items: center; justify-content: center; text-align: center; font-size: 20px; line-height: 26px; }

  /* Diamond types */
  .types { top: 1114px; height: 558px; background: var(--ink); color: var(--white); }
  .types .heading { top: 56px; color: var(--white); }
  .type-photo { top: 154px; width: 219px; height: 195px; }
  .type-name { top: 365px; width: 219px; text-align: center; font-size: 20px; }
  .btn-outline { left: 481px; top: 435px; width: 243px; height: 53px; border: 2px solid var(--white);
    display: flex; align-items: center; justify-content: center; font-size: 20px; color: var(--white); }

  /* Testimonials */
  .testimonials { top: 1672px; height: 505px; }
  .testimonials-photo { position: absolute; inset: 0;
    background:
      radial-gradient(ellipse 260px 300px at 1000px 220px, rgba(175,182,190,.5) 0%, rgba(175,182,190,0) 100%),
      radial-gradient(ellipse 300px 160px at 150px 430px, rgba(150,160,150,.45) 0%, rgba(150,160,150,0) 100%),
      linear-gradient(180deg, #e4e7ea 0%, #d6dadf 55%, #c4c8cb 100%); }
  .testimonials .heading { top: 45px; }
  .avatar { left: 527px; top: 152px; width: 149px; height: 149px; border-radius: 50%; border: 4px solid var(--white);
    background:
      radial-gradient(ellipse 40px 50px at 50% 48%, #e8b79c 0%, #d79a7e 60%, rgba(215,154,126,0) 100%),
      radial-gradient(ellipse 60px 70px at 50% 55%, #9a3f2c 0%, #7a2c22 60%, rgba(122,44,34,0) 100%),
      linear-gradient(180deg, #6f8fa8 0%, #8fa6b5 55%, #3b5f8e 100%); }
  .quote { left: 160px; width: 880px; top: 325px; text-align: center; font-size: 13px; line-height: 29px; color: var(--text-grey); }
  .dot { top: 405px; width: 21px; height: 21px; border-radius: 50%; background: var(--ink-soft); }
  .dot.is-muted { background: #666; }

  /* Gallery */
  .gallery { top: 2177px; height: 615px; background: var(--ink); }
  .gallery .heading { top: 42px; color: var(--white); }
  .gallery-item { width: 288px; height: 201px; }

  /* Contact */
  .contact { top: 2792px; height: 815px; }
  .contact-photo { position: absolute; inset: 0;
    background:
      radial-gradient(ellipse 600px 140px at 600px 620px, rgba(160,160,158,.5) 0%, rgba(160,160,158,0) 100%),
      linear-gradient(180deg, #e8e8e8 0%, #dcdcdc 40%, #cfcfcf 65%, #bdbdbc 85%, #c9c9c8 100%); }
  .contact .heading { top: 45px; }
  .contact-text { left: 190px; width: 820px; top: 143px; text-align: center; font-size: 13px; line-height: 29px; color: var(--text-grey); }
  .field { background: var(--white); font-size: 13px; color: var(--ink); padding: 20px 15px; }
  .btn-solid { left: 481px; top: 515px; width: 243px; height: 50px; background: var(--ink); color: var(--white);
    display: flex; align-items: center; justify-content: center; font-size: 20px; font-weight: 700; }
  .rule { left: 212px; top: 623px; width: 779px; height: 1px; background: #f5f5f5; }
  .social { top: 665px; width: 36px; height: 36px; border-radius: 50%; background: var(--ink); }
  .copyright { left: 0; width: 1200px; top: 745px; text-align: center; font-size: 12px; color: var(--text-grey); }
</style>
</head>
<body>

<header class="section site-nav">
  <div class="abs brand">LUNACREST<br>GEMS</div>
  <a class="abs nav-link is-active" style="left:363px">Home</a>
  <a class="abs nav-link" style="left:464px">About Us</a>
  <a class="abs nav-link" style="left:587px">Diamond Types</a>
  <a class="abs nav-link" style="left:748px">Testimonials</a>
  <a class="abs nav-link" style="left:892px">Gallery</a>
  <a class="abs nav-link" style="left:1003px">Contact Us</a>
</header>

<section class="section hero">
  <div class="hero-photo" role="img" aria-label="Sunset over a rocky New South Wales coastline"></div>
  <h1 class="heading hero-title">LUNACREST GEMS</h1>
  <p class="heading hero-sub">we are passionate about fine jewellery and gems.</p>
  <div class="abs hero-arrow" style="left:0">
    <svg width="20" height="36" viewBox="0 0 20 36"><polyline points="17,2 3,18 17,34" fill="none" stroke="#fff" stroke-width="2"/></svg>
  </div>
  <div class="abs hero-arrow" style="left:1125px">
    <svg width="20" height="36" viewBox="0 0 20 36"><polyline points="3,2 17,18 3,34" fill="none" stroke="#fff" stroke-width="2"/></svg>
  </div>
</section>

<section class="section about">
  <div class="about-photo" role="img" aria-label="Faded view of Sydney harbour and city skyline"></div>
  <h2 class="heading">ABOUT US</h2>
  <p class="abs about-text">At Lunacrest Gems we are passionate about fine jewellery and gems. We feature one of a kind, original and elegant, handmade pieces. Lunacrest Gems handmade jewellery is crafted using exceptional quality metals, integrating designs that are innovative, creative, and unique.</p>
</section>
<div class="abs service" style="left:176px">DIAMOND<br>ENGAGEMENT<br>RINGS</div>
<div class="abs service" style="left:510px">DIAMOND<br>ENGAGEMENT<br>JEWELLARY</div>
<div class="abs service" style="left:845px">NATIONAL<br>WIDE<br>SERVICES</div>

<section class="section types">
  <h2 class="heading">DIAMOND TYPES</h2>
  <div class="abs type-photo" style="left:130px;background:radial-gradient(circle at 40% 55%,#ffffff 0%,#cfd0d2 35%,#8f9296 75%,#6e7175 100%)" role="img" aria-label="Loose cut diamond"></div>
  <div class="abs type-photo" style="left:373px;background:radial-gradient(circle at 55% 45%,#ffffff 0%,#d9dbdf 30%,#9ea3a9 65%,#5d6268 100%)" role="img" aria-label="Scattered diamonds"></div>
  <div class="abs type-photo" style="left:611px;background:radial-gradient(circle at 50% 50%,#f4f8fc 0%,#c6d0db 35%,#7f8d9c 70%,#4b5663 100%)" role="img" aria-label="Pile of diamonds"></div>
  <div class="abs type-photo" style="left:849px;background:radial-gradient(circle at 60% 40%,#ffffff 0%,#e3e6e9 40%,#b4b9be 80%,#a0a5aa 100%)" role="img" aria-label="Small diamonds on silver"></div>
  <div class="abs type-name" style="left:130px">NONUMES</div>
  <div class="abs type-name" style="left:373px">ELABORARET</div>
  <div class="abs type-name" style="left:611px">MNESARCHUM</div>
  <div class="abs type-name" style="left:849px">VELIT ELIGENDI</div>
  <div class="abs btn-outline">VIEW ALL</div>
</section>

<section class="section testimonials">
  <div class="testimonials-photo" role="img" aria-label="Faded city skyline"></div>
  <h2 class="heading">TESTIMONIALS</h2>
  <div class="abs avatar" role="img" aria-label="Portrait of a customer"></div>
  <p class="abs quote">Ex vim dicat iudico. Adhuc atomorum in vim, oporteat elaboraret ut vis. Eam scripta numquam percipitur ad, ex qui putent accommodare, et eum quando tamquam lucilius. Vis eu exerci deserunt, aliquid omittam cu mei, malis animal singulis ut vel.</p>
  <div class="abs dot is-muted" style="left:553px"></div>
  <div class="abs dot" style="left:579px"></div>
  <div class="abs dot" style="left:606px"></div>
  <div class="abs dot" style="left:630px"></div>
</section>

<section class="section gallery">
  <h2 class="heading">GALLERY</h2>
  <div class="abs gallery-item" style="left:156px;top:139px;background:radial-gradient(ellipse at 50% 50%,#ffffff 0%,#f1f1f1 45%,#b9b9b9 80%,#8a8a8a 100%)" role="img" aria-label="Diamond band ring"></div>
  <div class="abs gallery-item" style="left:455px;top:139px;background:radial-gradient(ellipse at 50% 45%,#ffffff 0%,#dadde1 35%,#a6abb1 70%,#7a7f85 100%)" role="img" aria-label="Loose diamonds"></div>
  <div class="abs gallery-item" style="left:753px;top:139px;background:radial-gradient(ellipse at 40% 50%,#ffffff 0%,#e4e4e4 40%,#9a9a9a 75%,#f4f4f4 100%)" role="img" aria-label="Halo engagement ring"></div>
  <div class="abs gallery-item" style="left:156px;top:348px;background:radial-gradient(ellipse at 50% 55%,#d0d2d5 0%,#f2f3f4 35%,#ffffff 70%,#e9e9e9 100%)" role="img" aria-label="Pair of wedding rings"></div>
  <div class="abs gallery-item" style="left:455px;top:348px;background:radial-gradient(ellipse at 45% 50%,#f6f6f6 0%,#b5b5b5 35%,#5e5e5e 70%,#c9c9c9 100%)" role="img" aria-label="Cut diamond close up"></div>
  <div class="abs gallery-item" style="left:753px;top:348px;background:radial-gradient(ellipse at 50% 50%,#d7d7d7 0%,#f5f5f5 40%,#ffffff 75%,#f0f0f0 100%)" role="img" aria-label="Three stone diamond ring"></div>
</section>

<section class="section contact">
  <div class="contact-photo" role="img" aria-label="Faded coastal landscape"></div>
  <h2 class="heading">CONTACT US</h2>
  <p class="abs contact-text">Lorem ipsum dolor sit amet, no tollit nominavi delectus vix, quem platonem torquatos his et. Sed ei modo numquam eleifend, mei ex mundi tacimates suavitate</p>
  <div class="abs field" style="left:190px;top:231px;width:349px;height:60px">Name</div>
  <div class="abs field" style="left:190px;top:322px;width:349px;height:63px">E-mail</div>
  <div class="abs field" style="left:190px;top:409px;width:349px;height:63px">Phone</div>
  <div class="abs field" style="left:604px;top:231px;width:404px;height:241px">Message</div>
  <div class="abs btn-solid">SUBMIT</div>
  <div class="abs rule"></div>
  <div class="abs social" style="left:470px" aria-label="Social link"></div>
  <div class="abs social" style="left:526px" aria-label="Social link"></div>
  <div class="abs social" style="left:581px" aria-label="Social link"></div>
  <div class="abs social" style="left:636px" aria-label="Social link"></div>
  <div class="abs social" style="left:692px" aria-label="Social link"></div>
  <p class="abs copyright">© Copyright 2002-2012 Lunacrest Gems Pty Ltd.All Rights Reserved.</p>
</section>

</body>
</html>
```